We want to design total new business card and logo for Kestrel Building Services Ltd

Our company name Kestrel Building Services Ltd. Design new logo and business card , need hi-end luxury style art for architecture and construction industry. The card should simple but stylish. Our business focus on CONNECT tradesman to construction company, help marketing construction company tender oversea projects, managing franchise in construction sector, delivery amazing services to our client, so Logo should show the CONNECTION IDEA, CONNECTING PEOPLE, LUXURY. Visit our website for more information: kestrelgroup.example.nz

Target Market(s)

Directors or managers

Industry/Entity Type

Construction Company

Contact Information for Business Card

Name, Title, Mobile, Email, Website

Font styles to use
Serif

Colors

Designer to choose colors to be used in the design.

Requirements
Must have
• Simple and luxury, connection icon
Nice to have
• Special materials, plastic card, look through,...
• Look new ideas.

```html
<!DOCTYPE html>
<html lang="en">
<head>
<meta charset="utf-8">
<title>Kestrel Building Services Ltd – Business Card</title>
<link rel="stylesheet" href="https://fonts.googleapis.com/css2?family=Open+Sans:wght@400;600&display=swap">
<style>
  :root {
    --backdrop: #dfe2e6;
    --card: #f4f5f6;
    --navy: #1e3f95;
    --deep-blue: #1b4fa8;
    --sky: #3aa2cf;
    --ink: #333a40;
    --muted: #5a6168;
  }
  html, body {
    margin: 0;
    width: 1200px;
    height: 971px;
    overflow: hidden;
    background: var(--backdrop);
    font-family: "Open Sans", Arial, sans-serif;
  }
  .card {
    position: absolute;
    left: 150px;
    top: 225px;
    width: 900px;
    height: 520px;
    background: var(--card);
    border-radius: 22px;
    overflow: hidden;
    box-shadow: 0 10px 30px rgba(20, 30, 50, 0.18);
  }
  .edge-bar {
    position: absolute;
    left: 0;
    top: 250px;
    width: 9px;
    height: 270px;
    background: var(--navy);
  }
  .brand {
    position: absolute;
    left: 62px;
    top: 70px;
    display: flex;
    align-items: center;
    gap: 14px;
  }
  .brand-square {
    width: 26px;
    height: 26px;
    background: var(--navy);
    flex: none;
  }
  .brand-name {
    font-weight: 600;
    font-size: 28px;
    line-height: 32px;
    color: var(--navy);
    letter-spacing: 0.5px;
  }
  .person {
    position: absolute;
    left: 62px;
    top: 220px;
  }
  .person-name {
    margin: 0;
    font-weight: 600;
    font-size: 30px;
    color: var(--navy);
  }
  .person-title {
    margin: 4px 0 0;
    font-size: 21px;
    color: var(--muted);
  }
  .divider {
    position: absolute;
    left: 62px;
    top: 318px;
    width: 34px;
    height: 3px;
    background: var(--ink);
  }
  .address {
    position: absolute;
    left: 78px;
    top: 338px;
    margin: 0;
    font-size: 22px;
    line-height: 32px;
    color: var(--ink);
    font-style: normal;
  }
  .contacts {
    position: absolute;
    left: 82px;
    top: 420px;
    margin: 0;
    padding: 0;
    list-style: none;
    font-size: 21px;
    color: var(--ink);
  }
  .contacts li {
    display: flex;
    align-items: center;
    gap: 10px;
    height: 30px;
  }
  .contacts svg { width: 20px; height: 20px; }
  .mark-area {
    position: absolute;
    left: 440px;
    top: 0;
    width: 460px;
    height: 520px;
    background: linear-gradient(150deg, var(--sky) 0%, var(--deep-blue) 60%, var(--navy) 100%);
    clip-path: polygon(40% 0, 100% 0, 100% 100%, 0 100%);
    opacity: 0.9;
  }
</style>
</head>
<body>
  <main class="card">
    <div class="edge-bar"></div>

    <div class="brand">
      <span class="brand-square"></span>
      <span class="brand-name">Kestrel Building<br>Services Ltd</span>
    </div>

    <div class="person">
      <p class="person-name">Daniel Whitford</p>
      <p class="person-title">Managing Director</p>
    </div>

    <div class="divider"></div>

    <address class="address">
      18 Harbour View Lane, Riverton<br>
      Auckland 2099, New Zealand
    </address>

    <ul class="contacts">
      <li>
        <svg viewBox="0 0 24 24" aria-hidden="true"><path fill="#1e3f95" d="M6.6 10.8a15 15 0 0 0 6.6 6.6l2.2-2.2a1 1 0 0 1 1-.25 11.4 11.4 0 0 0 3.6.6 1 1 0 0 1 1 1V20a1 1 0 0 1-1 1A17 17 0 0 1 3 4a1 1 0 0 1 1-1h3.5a1 1 0 0 1 1 1c0 1.25.2 2.45.6 3.6a1 1 0 0 1-.25 1z"/></svg>
        0800 555 014
      </li>
      <li>
        <svg viewBox="0 0 24 24" aria-hidden="true"><rect x="3" y="5" width="18" height="14" fill="none" stroke="#1e3f95" stroke-width="2"/><path d="M3 6l9 7 9-7" fill="none" stroke="#1e3f95" stroke-width="2"/></svg>
        info@kestrelgroup.example.nz
      </li>
      <li>
        <svg viewBox="0 0 24 24" aria-hidden="true"><circle cx="12" cy="12" r="9" fill="none" stroke="#3aa2cf" stroke-width="2"/><path d="M3 12h18M12 3c3 3 3 15 0 18M12 3c-3 3-3 15 0 18" fill="none" stroke="#3aa2cf" stroke-width="1.6"/></svg>
        www.kestrelgroup.example.nz
      </li>
    </ul>

    <div class="mark-area" role="img" aria-label="Large brand mark in navy and sky blue"></div>
  </main>
</body>
</html>
```